New Business Card Design Project

Use the flyer uploaded and website www.brightoakbuilders.com for inspiration.
List Our Services on Backside of business cards
Marcus Delling
Harborline Builders Inc.
Licensed General Contractors
858-471-6093

Contact Information for Business Card

Use the flyer uploaded and website www.brightoakbuilders.com for inspiration. List Our Services on Backside of business cards Marcus Delling Harborline Builders Inc. Licensed General Contractors 858-471-6093

```html
<!DOCTYPE html>
<html lang="en">
<head>
<meta charset="utf-8">
<title>Harborline Builders – Business Cards</title>
<link rel="stylesheet" href="https://fonts.googleapis.com/css2?family=Cormorant+Garamond:wght@400;500&family=Arimo:wght@400;700&display=swap">
<style>
  :root {
    --stage: #3b3b3b;
    --card: #2d2d2e;
    --ink: #f4f4f4;
    --ink-soft: #d9d9d9;
    --rule: #bdbdbd;
  }
  * { box-sizing: border-box; margin: 0; padding: 0; }
  html, body {
    width: 1200px; height: 689px; overflow: hidden;
    background: var(--stage);
  }
  .canvas {
    width: 1200px; height: 689px;
    display: flex; align-items: center; justify-content: center; gap: 60px;
  }
  .card {
    width: 525px; height: 300px;
    background: var(--card);
    border-radius: 16px;
    color: var(--ink);
    position: relative;
    overflow: hidden;
  }

  /* Back side: company name and services */
  .card--services {
    display: flex; flex-direction: column; align-items: center;
    padding: 70px 28px 0;
    text-align: center;
  }
  .brand-name {
    display: flex; align-items: center; gap: 12px;
    font-family: "Cormorant Garamond", serif;
    font-weight: 400;
    font-size: 34px;
    letter-spacing: 2px;
    text-transform: uppercase;
    color: var(--ink);
  }
  .brand-mark {
    width: 14px; height: 14px;
    border: 1.5px solid var(--ink);
  }
  .services {
    margin-top: 58px;
    font-family: "Arimo", sans-serif;
    font-size: 12px;
    line-height: 1.45;
    color: var(--ink-soft);
  }
  .services strong { color: var(--ink); font-weight: 700; }

  /* Front side: contact details */
  .card--contact { padding: 48px 40px; }
  .person-name {
    font-family: "Cormorant Garamond", serif;
    font-weight: 500;
    font-size: 27px;
    text-transform: uppercase;
    letter-spacing: 0.5px;
    line-height: 1;
  }
  .person-role {
    font-family: "Arimo", sans-serif;
    font-size: 13px;
    color: var(--ink-soft);
    margin-top: 6px;
  }
  .divider {
    width: 32px; height: 1px;
    background: var(--rule);
    margin: 16px 0 14px;
  }
  .contact-list {
    list-style: none;
    font-family: "Arimo", sans-serif;
    font-size: 14px;
    line-height: 1.4;
    color: var(--ink);
  }
  .company-line {
    font-family: "Arimo", sans-serif;
    font-size: 13px;
    line-height: 1.4;
    color: var(--ink-soft);
  }
</style>
</head>
<body>
<main class="canvas">

  <section class="card card--services" aria-label="Card back with services">
    <h1 class="brand-name"><span class="brand-mark" aria-hidden="true"></span>Harborline Builders</h1>
    <p class="services">
      <strong>Remodel :</strong> Kitchen &amp; Bath | <strong>Painting :</strong> Interior &amp; Exterior | <strong>Flooring :</strong> Carpet, Vinyl, Wood<br>
      Window &amp; Door Replacement | <strong>Plumbing :</strong> Repairs &amp; Upgrades | Energy- Efficient Upgrades<br>
      Deck &amp; Patio Construction | Water &amp; Mold Damage | Garage Renovation
    </p>
  </section>

  <section class="card card--contact" aria-label="Card front with contact details">
    <h2 class="person-name">Marcus Delling</h2>
    <p class="person-role">President</p>
    <div class="divider"></div>
    <ul class="contact-list">
      <li>858-471-6093</li>
      <li>info@brightoakbuilders.com</li>
      <li>www.brightoakbuilders.com</li>
    </ul>
    <div class="divider"></div>
    <p class="company-line">Harborline Builders Inc.<br>Licensed General Contractors</p>
  </section>

</main>
</body>
</html>
```